Web Developer Needs a Business Card Design

I need a personal business card design that represents me as a web developer for potential employers. I would like the background to be a dark color on the front for contrast with my logo and name. The back will have all my information along with a smaller version of the logo. I want something with a modern look and feel, not too conservative. This will be used for potential employers and freelance work.

Industry/Entity Type

Business

Contact Information for Business Card

Front should have my logo and name. The back should have all my personal information which would include: name: Tom Varulek, phone: 570-614-3098, email: tomvarulek@quillbox.net, website url: www.tomvarulek.net, logo, web developer.

Font styles to use
Sans Serif

Requirements
Must have
• Must include my logo. The color palette base color will be the logo color.

```html
<!DOCTYPE html>
<html lang="en">
<head>
<meta charset="utf-8">
<title>Tom Varulek – Business Card</title>
<link rel="stylesheet" href="https://fonts.googleapis.com/css2?family=Open+Sans:wght@400;600;700&display=swap">
<style>
  :root {
    --teal: #5cc2a8;
    --teal-dark: #47ab92;
    --ink: #0c0c0c;
    --band: #1c1c1c;
    --paper: #ffffff;
    --backdrop: #e6e4e1;
    --muted: #d9d9d9;
  }
  * { box-sizing: border-box; margin: 0; padding: 0; }
  html, body { width: 1200px; height: 913px; overflow: hidden; }
  body {
    background: var(--backdrop);
    font-family: "Open Sans", Arial, sans-serif;
    position: relative;
  }
  .card {
    position: absolute;
    width: 525px;
    height: 300px;
    top: 306px;
    border-radius: 4px;
    overflow: hidden;
    box-shadow: 0 10px 30px rgba(0,0,0,.18);
  }

  /* contact side */
  .card-contact { left: 50px; background: var(--paper); }
  .card-contact .teal-band {
    position: absolute; left: 0; top: 150px; width: 200px; height: 150px;
    background: var(--teal);
  }
  .card-contact .dark-band {
    position: absolute; left: 150px; top: 42px; right: 0; height: 118px;
    background: var(--band);
  }
  .card-contact .mark {
    position: absolute; left: 82px; top: 92px; width: 128px; height: 128px;
    border-radius: 50%; background: var(--paper);
    display: flex; align-items: center; justify-content: center;
  }
  .card-contact .mark span {
    width: 104px; height: 104px; border-radius: 50%; background: var(--teal);
  }
  .contact {
    position: absolute; right: 24px; top: 52px; text-align: right; color: var(--paper);
  }
  .contact .name { font-weight: 700; font-size: 19px; letter-spacing: .5px; text-transform: uppercase; line-height: 1.15; }
  .contact .role { font-weight: 700; font-size: 13px; color: var(--teal); text-transform: uppercase; margin-bottom: 4px; }
  .contact .line { font-size: 12.5px; line-height: 1.45; display: flex; justify-content: flex-end; align-items: center; gap: 6px; }
  .contact svg { width: 12px; height: 12px; fill: var(--teal); flex: none; }

  /* name side */
  .card-front { right: 50px; background: var(--ink); color: var(--paper); text-align: center; }
  .card-front .mark {
    width: 104px; height: 104px; margin: 44px auto 18px; border-radius: 50%;
    border: 8px solid var(--teal);
  }
  .card-front .name { font-size: 30px; font-weight: 400; letter-spacing: 3px; text-transform: uppercase; }
  .card-front .role { font-size: 15px; margin-top: 8px; color: var(--muted); letter-spacing: .5px; }
</style>
</head>
<body>
  <section class="card card-contact" aria-label="Contact side">
    <div class="teal-band"></div>
    <div class="dark-band"></div>
    <div class="mark"><span></span></div>
    <div class="contact">
      <p class="name">Tom Varulek</p>
      <p class="role">Web Developer</p>
      <p class="line">570-614-3098
        <svg viewBox="0 0 24 24" aria-hidden="true"><path d="M6.6 10.8a15.1 15.1 0 0 0 6.6 6.6l2.2-2.2c.3-.3.7-.4 1-.2 1.1.4 2.3.6 3.6.6.6 0 1 .4 1 1V20c0 .6-.4 1-1 1A17 17 0 0 1 3 4c0-.6.4-1 1-1h3.5c.6 0 1 .4 1 1 0 1.3.2 2.5.6 3.6.1.3 0 .7-.2 1z"/></svg></p>
      <p class="line">tomvarulek@quillbox.net
        <svg viewBox="0 0 24 24" aria-hidden="true"><path d="M2 5h20v14H2zm2 2v.5l8 5 8-5V7zm0 2.8V17h16V9.8l-8 5z"/></svg></p>
      <p class="line">www.tomvarulek.net
        <svg viewBox="0 0 24 24" aria-hidden="true"><path d="M12 2a10 10 0 1 0 0 20 10 10 0 0 0 0-20zm6.9 6h-3a15 15 0 0 0-1.3-3.9A8 8 0 0 1 18.9 8zM12 4c.8 1.2 1.5 2.5 1.9 4h-3.8c.4-1.5 1.1-2.8 1.9-4zM4.3 14a8 8 0 0 1 0-4h3.4a16 16 0 0 0 0 4zm.8 2h3a15 15 0 0 0 1.3 3.9A8 8 0 0 1 5.1 16zm3-8h-3a8 8 0 0 1 4.3-3.9A15 15 0 0 0 8.1 8zM12 20c-.8-1.2-1.5-2.5-1.9-4h3.8c-.4 1.5-1.1 2.8-1.9 4zm2.3-6H9.7a14 14 0 0 1 0-4h4.6a14 14 0 0 1 0 4zm.3 5.9a15 15 0 0 0 1.3-3.9h3a8 8 0 0 1-4.3 3.9zm1.7-5.9a16 16 0 0 0 0-4h3.4a8 8 0 0 1 0 4z"/></svg></p>
    </div>
  </section>

  <section class="card card-front" aria-label="Name side">
    <div class="mark"></div>
    <p class="name">Tom Varulek</p>
    <p class="role">Front-End Developer</p>
  </section>
</body>
</html>
```